Under Morning Lantern website

I need a website to sell my t-shirt designs. I have around 5 designs I plan to sell on my initial launch, but only 3 photos at the moment. I would love a main page with the product images below maybe a large nicely designed header image, showing products with their sizes, item name/description, a way to add to cart and a review system like stars below each product image. Maybe a share option to Photostream, Facebook, Twitter, Pinterest, etc. would be cool too. Also on the main page under the product images a section showcasing my Photostream photos for the company. Then a section where I will include an About Me video from like YouTube. Lastly, on the main page an option to join my Mailing List at the footer with links to my Facebook and Photostream social accounts, links to pages (About Me, Shop, Photostream page, & Contact Us) as well as Track Order.

The other 4 pages will be for an About Me, which is the video I will make later that will be from YouTube. Then the Shop page. Then the Photostream page showcasing all the photos I plan to use to market the products, and a Contact Us Page.

I plan to possibly connect this to Shopify, so showcasing payment options (Palo, Birch Pay, Wayfarer, etc.) would be nice.

Lastly, I don't plan on doing returns/exchanges so maybe an area showing that would be nice too. ALL SALES FINAL

Mobile Friendly!

1st image is logo and other 4 images are t-shirt designs

Coded - Design and coding required

5+ page

• Separate pages, No Refunds (All Sales Final), Add to Cart, Way to Purchase

```html
<!DOCTYPE html>
<html lang="en">
<head>
<meta charset="utf-8">
<title>Under Morning Lantern — Product Name</title>
<link href="https://fonts.googleapis.com/css2?family=Poppins:wght@300;400;500;600&family=Roboto:wght@400;500;700&display=swap" rel="stylesheet">
<style>
:root{
  --brand:#03a9e9;
  --ink:#222222;
  --text:#555555;
  --muted:#8a8a8a;
  --line:#e4e4e4;
  --star:#f39c12;
  --green:#6aa40c;
  --footer:#2c2c2c;
  --footer-base:#222222;
  --panel:#f5f5f5;
  --white:#ffffff;
}
*{box-sizing:border-box;margin:0;padding:0}
html,body{width:1200px;height:2221px;overflow:hidden}
body{position:relative;background:var(--white);font-family:"Poppins",sans-serif;color:var(--text)}
.abs{position:absolute}

/* header */
.hero{left:0;top:0;width:1200px;height:314px;background:var(--brand)}
.brand-mark{left:118px;top:44px;width:190px;font:600 19px/22px "Poppins",sans-serif;color:#111;letter-spacing:.3px}
.nav{left:355px;top:44px;width:635px;height:44px;background:var(--white);border-radius:22px;overflow:hidden;font:400 16px/44px "Roboto",sans-serif;color:var(--ink)}
.nav span{position:absolute;top:0}
.nav .active{color:var(--brand)}
.nav .active::after{content:"";position:absolute;left:50%;bottom:6px;width:4px;height:4px;margin-left:-2px;border-radius:50%;background:var(--brand)}
.nav .track{left:465px;width:170px;height:44px;background:#000;color:var(--white);text-align:center;border-radius:0 22px 22px 0}
.cart{left:1048px;top:54px}
.cart-count{left:1066px;top:47px;width:16px;height:16px;border-radius:50%;background:#000;color:var(--white);font:500 10px/16px "Roboto",sans-serif;text-align:center}
.page-title{left:0;top:196px;width:1200px;text-align:center;font:700 35px/44px "Roboto",sans-serif;color:var(--white)}
.crumbs{left:0;top:246px;width:1200px;text-align:center;font:400 16px/22px "Roboto",sans-serif;color:var(--white)}
.crumbs i{font-style:normal;margin:0 16px}

/* gallery */
.thumb{left:118px;width:68px;height:76px;background:var(--panel)}
.thumb.on{border:2px solid var(--brand);background:#eeeeee}
.shot{left:194px;top:372px;width:485px;height:455px;background:var(--panel)}
.shot-art{left:260px;top:415px;width:340px;height:365px;border-radius:40px 40px 6px 6px;background:radial-gradient(circle at 50% 30%,#ffffff,#e6e6e6 70%)}
.shot-label{left:220px;top:392px;font:400 14px/20px "Poppins",sans-serif;color:var(--brand)}

/* product info */
.p-name{left:726px;top:366px;font:400 30px/40px "Poppins",sans-serif;color:var(--ink)}
.stars{color:var(--star);letter-spacing:1px}
.p-rating{left:726px;top:415px;font-size:12px;line-height:18px}
.p-rating em{font-style:normal;color:var(--muted);margin-left:6px;font-size:12.5px}
.p-price{left:726px;top:444px;font:400 28px/38px "Poppins",sans-serif;color:var(--ink)}
.p-desc{left:726px;top:485px;width:330px;font:300 12.5px/24.6px "Poppins",sans-serif;color:var(--ink)}
.opt-label{left:726px;font:500 13px/18px "Roboto",sans-serif;color:#444;letter-spacing:.4px}
.swatch{width:19px;height:19px;border-radius:50%}
.size{font:500 12.5px/19px "Roboto",sans-serif;color:#444}
.size b{display:inline-block;vertical-align:middle;width:19px;height:19px;border:1px solid #bdbdbd;border-radius:50%;margin-right:7px;position:relative}
.clear{left:850px;top:652px;font:400 11.5px/16px "Roboto",sans-serif;color:var(--muted);letter-spacing:.4px}
.qty{left:727px;top:689px;width:56px;height:33px;border:1px solid var(--line);font:400 12px/31px "Roboto",sans-serif;color:var(--brand);padding-left:16px}
.qty s{text-decoration:none;position:absolute;right:0;width:16px;height:16px;border-left:1px solid var(--line);color:#444;text-align:center;font-size:10px;line-height:15px}
.btn{text-align:center;font:500 13.5px/33px "Roboto",sans-serif;color:var(--white);letter-spacing:.3px}
.add{left:792px;top:689px;width:190px;height:33px;background:var(--brand)}
.buy{left:727px;top:741px;width:254px;height:34px;background:#333}
.share{left:727px;top:795px;width:144px;height:32px;border:1px solid #cfcfcf}
.share i{position:absolute;top:12px;width:8px;height:8px;border-radius:50%;background:#777}

/* tabs & reviews */
.tab{top:889px;font:600 28px/40px "Poppins",sans-serif}
.tab.off{left:118px;color:#cfcfcf}
.tab.on{left:321px;color:var(--ink)}
.sub-h{font:400 15px/20px "Poppins",sans-serif;color:var(--ink)}
.score{left:122px;top:985px;font:500 26px/32px "Poppins",sans-serif;color:var(--green)}
.score small{font:400 12px/12px "Poppins",sans-serif;color:#444;margin-left:5px}
.row-stars{left:122px;font-size:12px;line-height:14px}
.row-stars u{text-decoration:none;color:#cccccc}
.bar{left:228px;width:351px;height:9px;background:#eeeeee}
.bar.full{background:var(--green)}
.pct{left:590px;font:300 11.5px/14px "Poppins",sans-serif;color:var(--muted)}
.notice{left:658px;top:986px;font:300 12px/18px "Poppins",sans-serif;color:var(--ink)}
.notice a{color:#e84c3d;text-decoration:none}
.avatar{left:126px;top:1270px;width:52px;height:52px;border-radius:50%;background:#d5d5d5}
.author{left:196px;top:1290px;font:300 12px/18px "Poppins",sans-serif;color:#444}
.author b{font-weight:500;color:var(--ink)}
.review-text{left:199px;top:1322px;width:860px;font:300 12.5px/24.6px "Poppins",sans-serif;color:#666}

/* related */
.related-h{left:0;top:1440px;width:1200px;text-align:center;font:400 32px/42px "Poppins",sans-serif;color:var(--ink)}
.card{top:1522px;width:221px;height:324px;border:1px solid var(--line);background:var(--white)}
.card.hover{background:#eef7fc;border-color:var(--brand)}
.tee{position:absolute;left:30px;top:30px;width:160px;height:165px;border-radius:26px 26px 4px 4px}
.tee.black{background:linear-gradient(160deg,#2a2a2a,#050505)}
.tee.white{background:linear-gradient(160deg,#f3f3f3,#d8d8d8)}
.card h3{position:absolute;left:35px;top:223px;font:500 15.5px/22px "Poppins",sans-serif;color:var(--ink)}
.card .stars{position:absolute;left:35px;top:248px;font-size:12px}
.card .stars u{text-decoration:none}
.card .price{position:absolute;left:35px;top:270px;font:600 17px/24px "Poppins",sans-serif;color:var(--ink)}
.hover-btn{width:42px;height:42px;border-radius:50%;border:2px solid var(--brand);background:var(--white)}
.hover-btn.fill{background:var(--brand)}

/* footer */
.footer{left:0;top:1929px;width:1200px;height:215px;background:var(--footer)}
.footer-base{left:0;top:2144px;width:1200px;height:77px;background:var(--footer-base)}
.policy{left:118px;top:1972px;width:200px;font:400 12.5px/26px "Roboto",sans-serif;color:var(--brand)}
.f-rule{left:115px;top:2036px;width:193px;height:1px;background:#444}
.f-contact{left:118px;top:2052px;font:400 13px/24px "Roboto",sans-serif;color:#bbbbbb}
.f-div{top:1977px;width:1px;height:140px;background:#3e3e3e}
.f-head{font:400 15px/20px "Roboto",sans-serif;color:var(--white)}
.f-links{left:371px;top:2010px;font:400 13.5px/23px "Roboto",sans-serif;color:#bbbbbb}
.f-note{left:522px;top:2001px;font:400 13.5px/20px "Roboto",sans-serif;color:#bbbbbb}
.news{left:513px;top:2038px;width:364px;height:37px;border-radius:19px;background:var(--white);overflow:hidden}
.news span{position:absolute;left:26px;top:0;font:400 13.5px/37px "Roboto",sans-serif;color:#888}
.news b{position:absolute;left:245px;top:0;width:119px;height:37px;background:var(--brand);color:var(--white);font:500 14px/37px "Roboto",sans-serif;text-align:center;border-radius:0 19px 19px 0}
.f-social i{position:absolute;top:2094px;width:11px;height:11px;border-radius:50%;background:#9a9a9a}
.f-brand{left:951px;top:1973px;width:150px;font:600 17px/21px "Poppins",sans-serif;color:var(--brand);text-align:center}
.f-track{left:952px;top:2037px;width:136px;height:37px;background:var(--brand);color:var(--white);font:400 14px/37px "Roboto",sans-serif;text-align:center}
.copy{left:119px;top:2172px;font:400 13px/20px "Roboto",sans-serif;color:#9a9a9a}
.pay{top:2167px;width:48px;height:30px;border-radius:3px;background:var(--white);font:600 9.5px/30px "Poppins",sans-serif;color:#333;text-align:center}
</style>
</head>
<body>

<header>
  <div class="abs hero"></div>
  <div class="abs brand-mark">Under Morning<br>Lantern</div>
  <nav class="abs nav">
    <span style="left:46px">About</span>
    <span class="active" style="left:156px">Shop</span>
    <span style="left:251px">Photostream</span>
    <span style="left:357px">Contact</span>
    <span class="track">Track Order</span>
  </nav>
  <svg class="abs cart" width="26" height="26" viewBox="0 0 26 26" fill="none" stroke="#fff" stroke-width="1.8" stroke-linecap="round" stroke-linejoin="round"><path d="M2 4h3l3 12h12l3-9H7"/><circle cx="10" cy="21" r="1.6"/><circle cx="19" cy="21" r="1.6"/></svg>
  <div class="abs cart-count">0</div>
  <h1 class="abs page-title">PRODUCT NAME</h1>
  <div class="abs crumbs">Home<i>|</i>Shop<i>|</i>Product Name</div>
</header>

<section class="product">
  <div class="abs thumb" style="top:372px" role="img" aria-label="White t-shirt, front view"></div>
  <div class="abs thumb on" style="top:457px" role="img" aria-label="White t-shirt, back view"></div>
  <div class="abs shot"></div>
  <div class="abs shot-art" role="img" aria-label="White t-shirt back with a layered heart print"></div>
  <div class="abs shot-label">Back Design</div>

  <h2 class="abs p-name">Product Name</h2>
  <div class="abs p-rating"><span class="stars">★★★★☆</span><em>(18 customer review)</em></div>
  <div class="abs p-price">$99</div>
  <p class="abs p-desc">Lorem Ipsum is simply dummy text of the printing and typesetting industry. Lorem Ipsum has been the industry's</p>

  <div class="abs opt-label" style="top:566px">COLOR</div>
  <div class="abs swatch" style="left:807px;top:566px;background:#9b59c7"></div>
  <svg class="abs" style="left:811px;top:570px" width="11" height="11" viewBox="0 0 11 11" fill="none" stroke="#fff" stroke-width="1.6"><path d="M1.5 5.5l2.6 2.6L9.5 2.5"/></svg>
  <div class="abs swatch" style="left:843px;top:566px;background:#222"></div>
  <div class="abs swatch" style="left:881px;top:566px;background:#fff;border:1px solid #ccc"></div>
  <div class="abs swatch" style="left:917px;top:566px;background:var(--brand)"></div>
  <div class="abs swatch" style="left:954px;top:566px;background:#1fb3a8"></div>

  <div class="abs opt-label" style="top:618px">SIZE</div>
  <div class="abs size" style="left:806px;top:617px"><b><svg style="position:absolute;left:3px;top:3px" width="11" height="11" viewBox="0 0 11 11" fill="none" stroke="#333" stroke-width="1.4"><path d="M1.5 5.5l2.6 2.6L9.5 2.5"/></svg></b>S</div>
  <div class="abs size" style="left:875px;top:617px"><b></b>M</div>
  <div class="abs size" style="left:943px;top:617px"><b></b>L</div>
  <div class="abs size" style="left:1013px;top:617px"><b></b>XL</div>
  <div class="abs clear">CLEAR</div>

  <div class="abs qty">1<s style="top:0">+</s><s style="top:16px;border-top:1px solid var(--line)">-</s></div>
  <div class="abs btn add">ADD TO CART</div>
  <div class="abs btn buy">BUY NOW</div>
  <div class="abs share"><i style="left:20px"></i><i style="left:52px"></i><i style="left:84px"></i><i style="left:116px"></i></div>
</section>

<section class="reviews">
  <div class="abs tab off">Description</div>
  <div class="abs tab on">Reviews (1)</div>

  <div class="abs sub-h" style="left:122px;top:954px">Based On 1 Reviews</div>
  <div class="abs score">5.00<small>Overall</small></div>

  <div class="abs row-stars stars" style="top:1028px">★★★★★</div>
  <div class="abs bar full" style="top:1033px"></div>
  <div class="abs pct" style="top:1031px">100%</div>
  <div class="abs row-stars stars" style="top:1058px">★★★★<u>☆</u></div>
  <div class="abs bar" style="top:1063px"></div>
  <div class="abs pct" style="top:1061px;left:596px">0%</div>
  <div class="abs row-stars stars" style="top:1088px">★★★<u>☆☆</u></div>
  <div class="abs bar" style="top:1093px"></div>
  <div class="abs pct" style="top:1091px;left:596px">0%</div>
  <div class="abs row-stars stars" style="top:1118px">★★<u>☆☆☆</u></div>
  <div class="abs bar" style="top:1123px"></div>
  <div class="abs pct" style="top:1121px;left:596px">0%</div>
  <div class="abs row-stars stars" style="top:1148px">★<u>☆☆☆☆</u></div>
  <div class="abs bar" style="top:1153px"></div>
  <div class="abs pct" style="top:1151px;left:596px">0%</div>

  <div class="abs sub-h" style="left:658px;top:954px">Add A Review</div>
  <div class="abs notice">You must be <a>logged in</a> to post a review.</div>

  <div class="abs sub-h" style="left:126px;top:1225px">1 Review For Colorful Jacket</div>
  <div class="abs avatar"></div>
  <div class="abs stars" style="left:195px;top:1268px;font-size:12px">★★★★★</div>
  <div class="abs author"><b>Client Name</b> – January 14, 2020:</div>
  <p class="abs review-text">Lorem Ipsum is simply dummy text of the printing and typesetting industry. Lorem Ipsum has been the industry's standard dummy text ever since the 1500s, when an unknown printer took a galley of type and scrambled it to make a type specimen book. It has survived not only five centuries,</p>
</section>

<section class="related">
  <h2 class="abs related-h">Related Products</h2>
  <svg class="abs" style="left:1028px;top:1472px" width="14" height="20" viewBox="0 0 14 20" fill="none" stroke="#555" stroke-width="1.6"><path d="M10 2L3 10l7 8"/></svg>
  <svg class="abs" style="left:1059px;top:1472px" width="14" height="20" viewBox="0 0 14 20" fill="none" stroke="var(--brand)" stroke-width="1.8"><path d="M4 2l7 8-7 8"/></svg>

  <article class="abs card" style="left:119px">
    <div class="tee black" role="img" aria-label="Black t-shirt with lettered front print"></div>
    <h3>Product Name</h3><div class="stars">★★★<u>☆☆</u></div><div class="price">$120.00</div>
  </article>
  <article class="abs card hover" style="left:366px">
    <div class="tee black" role="img" aria-label="Black t-shirt with brand wordmark print"></div>
    <h3>Product Name</h3><div class="stars">★★★★☆</div><div class="price">$120.00</div>
  </article>
  <article class="abs card" style="left:613px">
    <div class="tee white" role="img" aria-label="White t-shirt, front and back with heart print"></div>
    <h3>Product Name</h3><div class="stars">★★★★★</div><div class="price">$120.00</div>
  </article>
  <article class="abs card" style="left:860px">
    <div class="tee black" role="img" aria-label="Black t-shirt with purple wordmark print"></div>
    <h3>Product Name</h3><div class="stars">★★★★☆</div><div class="price">$120.00</div>
  </article>

  <div class="abs hover-btn" style="left:529px;top:1544px"><svg style="position:absolute;left:11px;top:11px" width="16" height="16" viewBox="0 0 16 16" fill="none" stroke="#444" stroke-width="1.3"><path d="M1 6V1h5M10 1h5v5M15 10v5h-5M6 15H1v-5M1 1l14 14M15 1L1 15"/></svg></div>
  <div class="abs hover-btn" style="left:529px;top:1599px"><svg style="position:absolute;left:10px;top:11px" width="18" height="16" viewBox="0 0 18 16" fill="none" stroke="#444" stroke-width="1.4"><path d="M9 15S1 10 1 5a4 4 0 0 1 8-1 4 4 0 0 1 8 1c0 5-8 10-8 10z"/></svg></div>
  <div class="abs hover-btn fill" style="left:529px;top:1653px"><svg style="position:absolute;left:11px;top:12px" width="18" height="16" viewBox="0 0 18 16" fill="none" stroke="#fff" stroke-width="1.6" stroke-linecap="round"><path d="M1 2h3l2 8h9l2-6H5"/><circle cx="7" cy="14" r="1"/><circle cx="14" cy="14" r="1"/></svg></div>
</section>

<footer>
  <div class="abs footer"></div>
  <div class="abs policy">ALL SALES FINAL, NO REFUNDS,<br>RETURNS OR EXCHANGES</div>
  <div class="abs f-rule"></div>
  <div class="abs f-contact">+xxx xxxx xxxxx<br>xxxxxxx@postmail.com</div>
  <div class="abs f-div" style="left:325px"></div>
  <div class="abs f-head" style="left:371px;top:1975px">Contact Us</div>
  <div class="abs f-links">Home<br>About<br>Services<br>Contact</div>
  <div class="abs f-div" style="left:477px"></div>
  <div class="abs f-head" style="left:522px;top:1972px">Email Newsletter</div>
  <div class="abs f-note">Sale upto 20 % off for your next purchase inthis month!</div>
  <div class="abs news"><span>Email address</span><b>Subscribe</b></div>
  <div class="f-social"><i class="abs" style="left:523px"></i><i class="abs" style="left:556px"></i><i class="abs" style="left:588px"></i><i class="abs" style="left:616px"></i><i class="abs" style="left:645px"></i></div>
  <div class="abs f-div" style="left:905px"></div>
  <div class="abs f-brand">Under Morning<br>Lantern</div>
  <div class="abs f-track">Track Order</div>

  <div class="abs footer-base"></div>
  <div class="abs copy">© 2020 UML Under Morning Lantern &nbsp;| All Rights Reserved</div>
  <div class="abs pay" style="left:738px">Palo</div>
  <div class="abs pay" style="left:797px">Meridian</div>
  <div class="abs pay" style="left:857px">Corvo</div>
  <div class="abs pay" style="left:916px">Tallypay</div>
  <div class="abs pay" style="left:976px">Dunmore</div>
  <div class="abs pay" style="left:1035px">Wayfarer</div>
</footer>

</body>
</html>
```